New iOS App design for Boston Startup

We are looking for a new app design for our iPhone app. The current app's design feels outdated and we like to add lots of new functionality and a new navigation as well. A complete overhaul therefore!
We want you to design 5 screens that will have changed the most. The complete wireframes of these 5 pages are attached in the requirements document.
Once the winning design is selected we will award the winner with the designing all other screens (40-50 screens based on the same design). This will be a separate project worth $1000. The winning designer can get more follow up work if both sides are happy about the cooperation.
We will give feedback as soon as the first screen has been uploaded for review. Final decision will be made only after all 5 screens are finished.
We hope you give it your best!
Note: will only communicate through PixelHarbor (no skype),
Updates
Reason: Want to give designers a chance to submit their designs as I understand from some, the deadline is too close.
I have raised the award and introduced a 2nd price as well to make it worth your time. I hope you give it your best shot.
Reason: A few of you have asked for an extension of the deadline as time is running out. I will extend by one day. Tell me if you need more.
Industry/Entity Type
Startup
Requirements
Must have
- At least 1 screen before we can give you feedback.
Nice to have
- multiple options of 1 screen to get to a desirable design

```html
<!DOCTYPE html>
<html lang="en">
<head>
<meta charset="utf-8">
<title>Menu screen</title>
<link rel="stylesheet" href="https://fonts.googleapis.com/css2?family=Inter:wght@400;500;600&display=swap">
<style>
  :root {
    --page-bg: #eef1f4;
    --menu-blue: #2390d6;
    --header-blue: #1f86cb;
    --strip-blue: #3fb3e6;
    --row-line: rgba(255, 255, 255, 0.28);
    --white: #ffffff;
    --tab-bg: #f7f7f7;
    --tab-grey: #6f6f6f;
    --tab-active: #2186cf;
    --dot-on: #7fe3ff;
  }
  * { box-sizing: border-box; margin: 0; padding: 0; }
  html, body {
    width: 1200px; height: 802px; overflow: hidden;
    background: var(--page-bg);
    font-family: "Inter", "Helvetica Neue", Arial, sans-serif;
  }
  .screen {
    position: absolute; left: 393px; top: 33px;
    width: 414px; height: 736px;
    background: var(--menu-blue);
    overflow: hidden;
    box-shadow: 0 10px 30px rgba(0, 0, 0, 0.12);
  }
  .status-bar {
    height: 20px; display: flex; align-items: center; justify-content: space-between;
    padding: 0 8px; color: var(--white); font-size: 11px; font-weight: 500;
    background: var(--header-blue);
  }
  .status-bar .carrier, .status-bar .power { display: flex; align-items: center; gap: 4px; }
  .nav-bar {
    height: 44px; position: relative; display: flex; align-items: center; justify-content: center;
    background: var(--header-blue); color: var(--white); font-size: 17px; font-weight: 600;
    border-bottom: 1px solid var(--row-line);
  }
  .nav-bar .menu-toggle { position: absolute; left: 12px; top: 11px; }
  .drawer { position: absolute; top: 64px; left: 0; right: 0; bottom: 49px; display: flex; }
  .side-strip {
    width: 30px; background: var(--strip-blue);
    border-right: 1px solid var(--row-line);
    display: flex; flex-direction: column;
  }
  .side-strip .pager { height: 24px; display: flex; align-items: center; justify-content: center; gap: 2px; }
  .side-strip .pager span { width: 4px; height: 4px; border-radius: 50%; border: 1px solid var(--dot-on); }
  .side-strip .pager span.on { background: var(--dot-on); }
  .side-strip .ghost {
    height: 68px; border-bottom: 1px solid var(--row-line);
    display: flex; align-items: center; justify-content: center; opacity: 0.35;
  }
  .menu-list { flex: 1; list-style: none; padding-top: 24px;
    background: linear-gradient(100deg, rgba(80,200,240,0.45) 0%, rgba(80,200,240,0.12) 30%, rgba(0,0,0,0) 31%); }
  .menu-item {
    height: 68px; display: flex; align-items: center; gap: 16px;
    padding: 0 18px 0 16px; color: var(--white); font-size: 16px;
    border-bottom: 1px solid var(--row-line);
  }
  .menu-item .label { flex: 1; white-space: nowrap; }
  .menu-item svg { flex: none; }
  .tab-bar {
    position: absolute; left: 0; right: 0; bottom: 0; height: 49px;
    background: var(--tab-bg); border-top: 1px solid #dcdcdc;
    display: flex;
  }
  .tab { flex: 1; display: flex; flex-direction: column; align-items: center; justify-content: center;
    gap: 2px; font-size: 10px; color: #333; }
  .tab svg { color: var(--tab-grey); }
  .tab.active svg { color: var(--tab-active); }
</style>
</head>
<body>
<main class="screen">
  <div class="status-bar">
    <div class="carrier">
      <svg width="22" height="6" viewBox="0 0 22 6"><g fill="#fff"><circle cx="3" cy="3" r="2.5"/><circle cx="10" cy="3" r="2.5"/><circle cx="17" cy="3" r="2.5"/></g></svg>
      <span>ROAM</span>
      <svg width="12" height="9" viewBox="0 0 12 9" fill="none" stroke="#fff" stroke-width="1.4"><path d="M1 3.5a7 7 0 0 1 10 0M3 5.5a4 4 0 0 1 6 0"/><circle cx="6" cy="7.6" r="0.9" fill="#fff"/></svg>
    </div>
    <span class="time">4:21 PM</span>
    <div class="power">
      <svg width="7" height="11" viewBox="0 0 7 11" fill="none" stroke="#fff" stroke-width="1"><path d="M1 3l5 5-2.5 2V1L6 3 1 8"/></svg>
      <span>100%</span>
      <svg width="24" height="11" viewBox="0 0 24 11"><rect x="0.5" y="0.5" width="20" height="10" rx="2" fill="none" stroke="#fff"/><rect x="2" y="2" width="17" height="7" rx="1" fill="#fff"/><rect x="21.5" y="3.5" width="2" height="4" fill="#fff"/></svg>
    </div>
  </div>

  <header class="nav-bar">
    <svg class="menu-toggle" width="24" height="22" viewBox="0 0 24 22" stroke="#fff" stroke-width="2.6" stroke-linecap="round"><path d="M2 4h20M2 11h20M2 18h20"/></svg>
    <h1 style="font-size:17px;font-weight:600">Menu</h1>
  </header>

  <div class="drawer">
    <div class="side-strip" aria-hidden="true">
      <div class="pager"><span></span><span></span><span class="on"></span><span class="on"></span></div>
      <div class="ghost"><svg width="16" height="16" viewBox="0 0 16 16" fill="none" stroke="#fff"><path d="M2 14L8 3l6 11z"/></svg></div>
      <div class="ghost"><svg width="16" height="16" viewBox="0 0 16 16" fill="none" stroke="#fff"><rect x="2" y="4" width="12" height="9"/></svg></div>
      <div class="ghost"><svg width="16" height="16" viewBox="0 0 16 16" fill="none" stroke="#fff"><path d="M3 13l9-9 1 1-9 9z"/></svg></div>
      <div class="ghost"><svg width="16" height="16" viewBox="0 0 16 16" fill="none" stroke="#fff"><path d="M3 13L13 3"/></svg></div>
      <div class="ghost"><svg width="16" height="16" viewBox="0 0 16 16" fill="none" stroke="#fff"><circle cx="8" cy="8" r="5"/></svg></div>
      <div class="ghost"><svg width="16" height="16" viewBox="0 0 16 16" fill="none" stroke="#fff"><circle cx="8" cy="8" r="5"/><path d="M3 8h10"/></svg></div>
      <div class="ghost"><svg width="16" height="16" viewBox="0 0 16 16" fill="none" stroke="#fff"><circle cx="8" cy="8" r="3"/></svg></div>
      <div class="ghost"><svg width="16" height="16" viewBox="0 0 16 16" fill="none" stroke="#fff"><circle cx="8" cy="8" r="6"/></svg></div>
    </div>

    <ul class="menu-list">
      <li class="menu-item">
        <svg width="28" height="28" viewBox="0 0 28 28" fill="none" stroke="#fff" stroke-width="1.3" stroke-linejoin="round"><path d="M2 10l12-5 12 5-12 5z"/><path d="M7 12v6c2 3 12 3 14 0v-6"/><path d="M25 10v7"/></svg>
        <span class="label">Profile</span>
        <svg width="9" height="14" viewBox="0 0 9 14" fill="none" stroke="#fff" stroke-width="1.8"><path d="M1.5 1.5L7 7l-5.5 5.5"/></svg>
      </li>
      <li class="menu-item">
        <svg width="28" height="28" viewBox="0 0 28 28" fill="none" stroke="#fff" stroke-width="1.3"><circle cx="14" cy="9" r="5"/><path d="M4 25c0-6 4-9 10-9s10 3 10 9z"/></svg>
        <span class="label">My Tutor</span>
        <svg width="9" height="14" viewBox="0 0 9 14" fill="none" stroke="#fff" stroke-width="1.8"><path d="M1.5 1.5L7 7l-5.5 5.5"/></svg>
      </li>
      <li class="menu-item">
        <svg width="28" height="28" viewBox="0 0 28 28" fill="none" stroke="#fff" stroke-width="1.3" stroke-linejoin="round"><path d="M18 3l5 5-13 13-6 1 1-6z"/><path d="M15 6l5 5"/></svg>
        <span class="label">Advanced Writing Assignment(AWA)</span>
        <svg width="9" height="14" viewBox="0 0 9 14" fill="none" stroke="#fff" stroke-width="1.8"><path d="M1.5 1.5L7 7l-5.5 5.5"/></svg>
      </li>
      <li class="menu-item">
        <svg width="28" height="28" viewBox="0 0 28 28" fill="none" stroke="#fff" stroke-width="1.3" stroke-linejoin="round"><path d="M3 12h5v12H3z"/><path d="M8 13l5-9c2 0 3 2 2 5l-1 3h8c2 0 3 2 2 4l-2 6c-1 2-2 2-4 2H8"/></svg>
        <span class="label">Social</span>
        <svg width="9" height="14" viewBox="0 0 9 14" fill="none" stroke="#fff" stroke-width="1.8"><path d="M1.5 1.5L7 7l-5.5 5.5"/></svg>
      </li>
      <li class="menu-item">
        <svg width="28" height="28" viewBox="0 0 28 28" fill="none" stroke="#fff" stroke-width="1.3"><path d="M14 3c6 0 11 4 11 10s-5 10-11 10c-2 0-3 0-5-1l-5 2 2-4c-2-2-3-4-3-7 0-6 5-10 11-10z"/><path d="M11 10c0-2 1-3 3-3s3 1 3 3c0 2-3 2-3 4M14 17v1"/></svg>
        <span class="label">Vocabulary</span>
        <svg width="9" height="14" viewBox="0 0 9 14" fill="none" stroke="#fff" stroke-width="1.8"><path d="M1.5 1.5L7 7l-5.5 5.5"/></svg>
      </li>
      <li class="menu-item">
        <svg width="28" height="28" viewBox="0 0 28 28" fill="none" stroke="#fff" stroke-width="1.3"><circle cx="14" cy="14" r="11"/><ellipse cx="14" cy="14" rx="5" ry="11"/><path d="M3 14h22M5 8h18M5 20h18"/></svg>
        <span class="label">Marketplace</span>
        <svg width="9" height="14" viewBox="0 0 9 14" fill="none" stroke="#fff" stroke-width="1.8"><path d="M1.5 1.5L7 7l-5.5 5.5"/></svg>
      </li>
      <li class="menu-item">
        <svg width="28" height="28" viewBox="0 0 28 28" fill="none" stroke="#fff" stroke-width="1.3" stroke-linejoin="round"><path d="M12 2h4l1 4 3 1 3-2 3 3-2 3 1 3 4 1v4l-4 1-1 3 2 3-3 3-3-2-3 1-1 4h-4l-1-4-3-1-3 2-3-3 2-3-1-3-4-1v-4l4-1 1-3-2-3 3-3 3 2 3-1z" transform="scale(0.92) translate(1.2 1.2)"/><circle cx="14" cy="14" r="4"/></svg>
        <span class="label">Settings</span>
        <svg width="9" height="14" viewBox="0 0 9 14" fill="none" stroke="#fff" stroke-width="1.8"><path d="M1.5 1.5L7 7l-5.5 5.5"/></svg>
      </li>
      <li class="menu-item">
        <svg width="28" height="28" viewBox="0 0 28 28" fill="none" stroke="#fff" stroke-width="1.3"><circle cx="14" cy="14" r="11"/><path d="M14 12v8M14 8v1.5" stroke-width="2"/></svg>
        <span class="label">About the MBAX</span>
        <svg width="9" height="14" viewBox="0 0 9 14" fill="none" stroke="#fff" stroke-width="1.8"><path d="M1.5 1.5L7 7l-5.5 5.5"/></svg>
      </li>
    </ul>
  </div>

  <nav class="tab-bar">
    <div class="tab">
      <svg width="26" height="22" viewBox="0 0 26 22" fill="currentColor"><path d="M13 1L1 11h4v10h6v-6h4v6h6V11h4z"/></svg>
      <span>Home</span>
    </div>
    <div class="tab">
      <svg width="28" height="22" viewBox="0 0 28 22" fill="none" stroke="currentColor" stroke-width="1.3"><path d="M14 4C10 1 5 1 2 2v17c3-1 8-1 12 2 4-3 9-3 12-2V2c-3-1-8-1-12 2zM14 4v17"/></svg>
      <span>Theory</span>
    </div>
    <div class="tab active">
      <svg width="24" height="22" viewBox="0 0 24 22" fill="currentColor"><path d="M2 5l10-4 10 4-10 4z"/><path d="M2 11l10-4 10 4-10 4z" opacity="0.85"/><path d="M2 17l10-4 10 4-10 4z" opacity="0.7"/></svg>
      <span>Practice</span>
    </div>
    <div class="tab">
      <svg width="30" height="22" viewBox="0 0 30 22" fill="currentColor"><path d="M8 3h14c4 0 7 5 7 11 0 5-3 7-6 4l-3-3H10l-3 3c-3 3-6 1-6-4C1 8 4 3 8 3z"/><path d="M9 7v6M6 10h6" stroke="#f7f7f7" stroke-width="2"/><circle cx="20" cy="8" r="1.4" fill="#f7f7f7"/><circle cx="23" cy="11" r="1.4" fill="#f7f7f7"/></svg>
      <span>Games</span>
    </div>
    <div class="tab">
      <svg width="26" height="22" viewBox="0 0 26 22" fill="currentColor"><circle cx="13" cy="11" r="10"/><path d="M8 11l4 4 7-8" fill="none" stroke="#f7f7f7" stroke-width="2.4"/></svg>
      <span>Test</span>
    </div>
  </nav>
</main>
</body>
</html>
```